Vernac Law Business cards and stationary design project

We are looking for a stationary design for business cards (double sided), 8x10, 5x7, and legal and standard envelopes.

We would like the design to match the logo that we have already.
Color palate preferred is Teal, White, grey and any others that will look good for a professional law firm.

We would like this statement: "RELATIONSHIPS. RESPECT. RESULT" to be on the back of the business cards and maybe on the stationary if it looks good.

Please see link to website for more information: www.vernac-law.example

Target Market(s)

Potential clients that need Attorney services.

Industry/Entity Type

Law Firm

Contact Information for Business Card

We would like the front and back to be two different colors. Current business cards are teal front, grey back and are a vertical design. We are open to options with colors.

Font styles to use
Serif

Colors
33a6d7
33b8a4
b9b9b9
5c5c5c

Requirements
Must have
• Logo supplied needs to go on the card and stationary.
• Match website color palate, www.vernac-law.example
• Be professional and not too wordy.
• Criminal Law, Civil Litigation, Personal Injury, Restraining Orders need to be on the card.
Nice to have
• RELATIONSHIPS. RESPECT. RESULTS. on the back of the card.
Should not have
• Not be too busy/wordy or too flashy.

```html
<!DOCTYPE html>
<html lang="en">
<head>
<meta charset="utf-8">
<title>Vernac Law Stationery</title>
<link href="https://fonts.googleapis.com/css2?family=Cinzel:wght@400;500&display=swap" rel="stylesheet">
<style>
  :root {
    --backdrop: #d3d3d3;
    --paper: #ffffff;
    --teal: #12869a;
    --teal-line: #5fb3c2;
    --charcoal: #53544f;
    --ink: #3c3c3c;
    --shadow: 3px 4px 8px rgba(0,0,0,.28);
  }
  * { margin: 0; padding: 0; box-sizing: border-box; }
  html, body { width: 1200px; height: 900px; overflow: hidden; }
  body {
    background: var(--backdrop);
    font-family: "Cinzel", serif;
    color: var(--ink);
    position: relative;
  }
  .piece { position: absolute; background: var(--paper); box-shadow: var(--shadow); overflow: hidden; }
  .band { position: absolute; left: 0; right: 0; bottom: 0; background: var(--charcoal); }
  .firm-name { color: var(--teal); font-weight: 400; letter-spacing: .04em; white-space: nowrap; }

  /* Envelope back */
  .envelope-back { left: 27px; top: 147px; width: 562px; height: 283px; }
  .envelope-back svg { position: absolute; left: 0; top: 0; }

  /* Envelope front */
  .envelope-front { left: 121px; top: 260px; width: 524px; height: 261px; }
  .envelope-front .firm-name { position: absolute; left: 24px; top: 70px; font-size: 19px; }
  .envelope-front .address { position: absolute; left: 21px; top: 115px; font-size: 10.5px; line-height: 13px; }
  .envelope-front .band { height: 18px; }

  /* Business card back */
  .card-back { left: 60px; top: 540px; width: 281px; height: 168px; text-align: center; }
  .card-back .practice-title { margin-top: 49px; color: var(--teal); font-size: 10.5px; letter-spacing: .26em; }
  .card-back .practice-list { list-style: none; margin-top: 12px; color: var(--teal); font-size: 7px; line-height: 9px; }
  .card-back .band { height: 24px; display: flex; align-items: center; justify-content: center; }
  .card-back .tagline { color: #e9e9e6; font-size: 10px; letter-spacing: .22em; }

  /* Business card front */
  .card-front { left: 358px; top: 540px; width: 283px; height: 169px; text-align: center; }
  .card-front .name-tab {
    position: absolute; left: 78px; top: 0; width: 127px; height: 83px;
    background: var(--teal); border-radius: 0 0 9px 9px;
    display: flex; align-items: flex-end; justify-content: center; padding-bottom: 16px;
  }
  .card-front .name-tab .firm-name { color: var(--paper); font-size: 13px; }
  .card-front .address { position: absolute; left: 0; right: 0; top: 93px; font-size: 8px; line-height: 11px; }
  .card-front .contact { position: absolute; left: 0; right: 0; top: 131px; font-size: 8px; line-height: 11px; }

  /* Letterhead */
  .letterhead { left: 669px; top: 118px; width: 473px; height: 667px; }
  .letterhead .firm-name { position: absolute; left: 0; right: 0; top: 76px; text-align: center; font-size: 19px; }
  .letterhead .rule { position: absolute; left: 32px; width: 409px; height: 1px; background: var(--teal-line); }
  .letterhead .rule.top { top: 125px; }
  .letterhead .rule.bottom { top: 150px; }
  .letterhead .address { position: absolute; left: 0; right: 0; top: 128px; text-align: center; font-size: 6.5px; line-height: 11px; }
  .letterhead .band { height: 18px; }
</style>
</head>
<body>
  <div class="piece envelope-back">
    <svg width="562" height="283" viewBox="0 0 562 283" aria-hidden="true">
      <polygon points="0,0 562,0 530,68 35,68" fill="var(--teal)"/>
    </svg>
  </div>

  <div class="piece envelope-front">
    <div class="firm-name">Vernac Law</div>
    <p class="address">
      Southern California,<br>
      480 Harbor Crest Ave. #210<br>
      Seacliff Bay, CA 90000<br>
      (555) 014-2870 &nbsp;| &nbsp;mara@vernac-law.example
    </p>
    <div class="band"></div>
  </div>

  <div class="piece card-back">
    <h2 class="practice-title">Practice Areas:</h2>
    <ul class="practice-list">
      <li>Criminal Law</li>
      <li>Civil Litigation / Personal Injury</li>
      <li>Restraining Orders</li>
    </ul>
    <div class="band"><span class="tagline">Relationships. Respect. Result.</span></div>
  </div>

  <div class="piece card-front">
    <div class="name-tab"><span class="firm-name">Vernac Law</span></div>
    <p class="address">
      Southern California,<br>
      480 Harbor Crest Ave. #210<br>
      Seacliff Bay, CA 90000
    </p>
    <p class="contact">
      (555) 014-2870<br>
      mara@vernac-law.example
    </p>
  </div>

  <div class="piece letterhead">
    <div class="firm-name">Vernac Law</div>
    <div class="rule top"></div>
    <p class="address">
      Southern California, 480 Harbor Crest Ave. #210 Seacliff Bay, CA 90000<br>
      (555) 014-2870 &nbsp;| &nbsp;mara@vernac-law.example
    </p>
    <div class="rule bottom"></div>
    <div class="band"></div>
  </div>
</body>
</html>
```